Business Card - Business Consultancy

Newly Established Company, specializing in Business Consultancy, Human Resource Management, Talent Acquisition and Payroll Solutions.

We need a Business card design which portrays "elegance" and a very sleek yet business-like design. We would like a nice blue trimming (which goes well with the logo) to separate the content of the business card at the top. We would also like to see the design using the color silver either as a background or incorporated into it.

The final design should be a Business card which has colors matching the logo; a nice font; the above-mentioned specifics that adheres to the theme of "a stylish and professional business"

FYI: please do not have too fanciful designs.

Industry/Entity Type

Business Consultant

Contact Information for Business Card

Darren Lim
Business Development Director
Arbor Talent Consulting Private Limited
27 Wexley Street, #05-03B
Harbourgate Trade Building
Singapore 059317
Mobile : (+65) 98354417
Email : dlim@arbortalent-advisory.com
Alternative : arbortalentadvisory@mailbox-example.com

Requirements
Must have
• Nice Blue Trimming matching Logo which separates content, see attached
• Design incorporates either a silver background or the use of the color silver
Should not have
• No Fanciful Designs
• No Childish Designs
• No Overly Complicated Designs

```html
<!DOCTYPE html>
<html lang="en">
<head>
<meta charset="UTF-8">
<title>Arbor Talent Consulting — Business Card</title>
<link href="https://fonts.googleapis.com/css2?family=Open+Sans:wght@400;600;700&display=swap" rel="stylesheet">
<style>
  :root {
    --backdrop: #2c2e33;
    --card-white: #ffffff;
    --silver-light: #f4f5f6;
    --silver: #dcdfe2;
    --trim-blue: #2b80e8;
    --name-blue: #1f7fc4;
    --ink: #1c1c1c;
    --brand-grey: #3a3a3c;
    --leaf-green: #8cc63f;
  }
  * { box-sizing: border-box; margin: 0; padding: 0; }
  html, body {
    width: 1200px; height: 864px; overflow: hidden;
    background: var(--backdrop);
    font-family: "Open Sans", Arial, sans-serif;
  }
  .canvas { position: relative; width: 1200px; height: 864px; }

  .card {
    position: absolute;
    width: 560px; height: 320px;
    overflow: hidden;
    box-shadow: 0 10px 28px rgba(0,0,0,0.45);
  }

  /* Front */
  .card-front { left: 230px; top: 70px; background: var(--card-white); }
  .card-front .brand {
    position: absolute; left: 0; right: 0; top: 78px;
    display: flex; justify-content: center; align-items: center; gap: 14px;
  }
  .brand-dot {
    width: 58px; height: 58px; border-radius: 50%;
    background: var(--trim-blue);
  }
  .brand-name {
    font-weight: 700; color: var(--brand-grey);
    font-size: 34px; letter-spacing: 1px; line-height: 1;
  }
  .trim-band {
    position: absolute; left: 0; right: 0; top: 196px; height: 60px;
    background: var(--trim-blue);
    display: flex; align-items: center; justify-content: center;
    text-align: center;
    color: #fff; font-weight: 600; font-size: 16px; line-height: 1.25;
  }
  .silver-foot {
    position: absolute; left: 0; right: 0; bottom: 0; height: 46px;
    background: linear-gradient(180deg, var(--card-white), var(--silver-light));
  }

  /* Back */
  .card-back {
    left: 200px; top: 470px;
    background: linear-gradient(135deg, var(--card-white) 0%, var(--silver-light) 55%, var(--silver) 100%);
  }
  .card-back .brand {
    position: absolute; right: 40px; top: 40px;
    display: flex; align-items: center; gap: 12px;
  }
  .card-back .brand-dot { width: 48px; height: 48px; }
  .card-back .brand-name { font-size: 28px; }

  .person { position: absolute; left: 78px; top: 132px; }
  .person-name { color: var(--name-blue); font-weight: 600; font-size: 19px; line-height: 1.2; }
  .person-title { color: var(--ink); font-size: 13.5px; }

  .contacts {
    position: absolute; right: 40px; top: 200px;
    list-style: none; text-align: right;
    color: var(--ink); font-size: 13.5px; line-height: 21px;
  }
  .contacts li { display: flex; justify-content: flex-end; align-items: center; gap: 8px; }
  .contacts svg { width: 12px; height: 12px; fill: var(--name-blue); flex: none; }

  .address {
    position: absolute; left: 40px; right: 40px; bottom: 26px;
    color: var(--ink); font-size: 13.5px;
  }
</style>
</head>
<body>
<main class="canvas">

  <section class="card card-front" aria-label="Card front">
    <div class="brand">
      <span class="brand-dot"></span>
      <span class="brand-name">Arbor Talent</span>
    </div>
    <div class="trim-band">
      <p>Recruitment | HR Solutions | Business<br>Consultancy</p>
    </div>
    <div class="silver-foot"></div>
  </section>

  <section class="card card-back" aria-label="Card back">
    <div class="brand">
      <span class="brand-dot"></span>
      <span class="brand-name">Arbor Talent</span>
    </div>

    <div class="person">
      <p class="person-name">Darren Lim</p>
      <p class="person-title">Business Development Director</p>
    </div>

    <ul class="contacts">
      <li>(+65) 98354417
        <svg viewBox="0 0 24 24" aria-hidden="true"><path d="M6.6 10.8a15.1 15.1 0 0 0 6.6 6.6l2.2-2.2c.3-.3.7-.4 1-.2 1.1.4 2.3.6 3.6.6.6 0 1 .4 1 1V20c0 .6-.4 1-1 1A17 17 0 0 1 3 4c0-.6.4-1 1-1h3.5c.6 0 1 .4 1 1 0 1.3.2 2.5.6 3.6.1.3 0 .7-.2 1z"/></svg>
      </li>
      <li>dlim@arbortalent-advisory.com
        <svg viewBox="0 0 24 24" aria-hidden="true"><path d="M2 5h20v14H2z" /><path d="M2 5l10 8 10-8" fill="none" stroke="#fff" stroke-width="2"/></svg>
      </li>
      <li>arbortalentadvisory@mailbox-example.com
        <svg viewBox="0 0 24 24" aria-hidden="true"><path d="M2 5h20v14H2z" /><path d="M2 5l10 8 10-8" fill="none" stroke="#fff" stroke-width="2"/></svg>
      </li>
    </ul>

    <p class="address">27 Wexley Street, #05-03B Harbourgate Trade Building Singapore 059317</p>
  </section>

</main>
</body>
</html>
```